Business Card and Letterhead for Pimlu - modern real estate business

I need a double sided business card design for Pimlu. Please see business card brief here https://files.trelvonadocs.com/sheet/r/7QzTmWbaXLJnoPEd-kRyUgFhHsstbvCe2qfoMxDa_pz/view?mode=shared

Please feel free to design the business cards however you feel best. I am happy to give some creative freedoms and then provide feedback from there.

Please then also create a letterhead to match the business card design

Colors

Designer to choose colors to be used in the design.

Requirements
Must have
• Must be a modern, elegant business card which looks very professional

```html
<!DOCTYPE html>
<html lang="en">
<head>
<meta charset="UTF-8">
<title>Pimlu – Business Card</title>
<link href="https://fonts.googleapis.com/css2?family=Michroma&family=Montserrat:wght@400;500&display=swap" rel="stylesheet">
<style>
  :root {
    --page-bg: #2a2a2a;
    --card-black: #050505;
    --stripe-grey: #262626;
    --brand-red: #e21f2b;
    --paper-white: #ffffff;
    --ink-dark: #222222;
    --ink-light: #f2f2f2;
    --photo-top: #8fa27a;
    --photo-bottom: #2b2b2b;
  }
  * { margin: 0; padding: 0; box-sizing: border-box; }
  html, body {
    width: 1200px; height: 900px; overflow: hidden;
    background: var(--page-bg);
  }
  .stage {
    width: 1200px; height: 900px;
    display: flex; flex-direction: column; align-items: center; justify-content: center;
    gap: 34px;
  }
  .card {
    position: relative;
    width: 700px; height: 400px;
    overflow: hidden;
    box-shadow: 0 10px 30px rgba(0,0,0,.45);
  }

  /* Front side */
  .card-front { background: var(--card-black); }
  .card-front .stripes { position: absolute; inset: 0; }
  .wordmark {
    font-family: "Michroma", sans-serif;
    color: var(--brand-red);
    letter-spacing: 0.04em;
    line-height: 1;
  }
  .card-front .wordmark {
    position: absolute; left: 0; right: 0; top: 130px;
    text-align: center; font-size: 92px;
  }
  .card-front .site {
    position: absolute; left: 0; right: 0; bottom: 34px;
    text-align: center;
    font-family: "Montserrat", sans-serif; font-size: 15px; font-weight: 500;
    color: var(--ink-light); letter-spacing: 0.06em;
  }
  .site .accent { color: var(--brand-red); }

  /* Back side */
  .card-back { background: var(--paper-white); }
  .back-header {
    position: absolute; left: 0; top: 0; width: 100%; height: 200px;
    background: var(--card-black);
    border-bottom: 3px solid var(--brand-red);
  }
  .portrait-frame {
    position: absolute; left: 42px; top: 24px;
    width: 158px; height: 158px;
    border: 1px solid var(--brand-red);
    padding: 6px;
  }
  .portrait {
    width: 100%; height: 100%;
    border: 5px solid var(--paper-white);
    background: linear-gradient(180deg, var(--photo-top) 0%, #6c7a5e 45%, var(--photo-bottom) 100%);
  }
  .back-header .wordmark {
    position: absolute; right: 40px; bottom: 26px; font-size: 40px;
  }
  .side-tab {
    position: absolute; left: 0; top: 206px;
    width: 10px; height: 38px; background: var(--card-black);
  }
  .agent { position: absolute; left: 44px; top: 222px; }
  .agent-name {
    font-family: "Michroma", sans-serif; font-size: 24px;
    color: var(--brand-red); letter-spacing: 0.03em;
  }
  .agent-role {
    font-family: "Montserrat", sans-serif; font-size: 17px;
    color: var(--ink-dark); margin-top: 2px;
  }
  .contact {
    position: absolute; right: 36px; top: 262px;
    font-family: "Montserrat", sans-serif; font-size: 18px;
    color: var(--ink-dark); text-align: right; line-height: 1.25;
  }
  .address { margin-right: 30px; margin-bottom: 10px; }
  .contact-line { display: flex; align-items: center; justify-content: flex-end; gap: 14px; }
  .contact-line svg { width: 16px; height: 16px; flex: none; }
</style>
</head>
<body>
<main class="stage">

  <section class="card card-front" aria-label="Business card front">
    <svg class="stripes" viewBox="0 0 700 400" aria-hidden="true">
      <polygon points="215,0 240,0 95,400 70,400" fill="var(--stripe-grey)"/>
      <polygon points="300,0 322,0 380,150 358,150" fill="var(--stripe-grey)"/>
    </svg>
    <div class="wordmark">PIMLU</div>
    <div class="site">www.<span class="accent">pimlu</span>.com</div>
  </section>

  <section class="card card-back" aria-label="Business card back">
    <div class="back-header">
      <div class="portrait-frame">
        <div class="portrait" role="img" aria-label="Portrait photo of the agent in a dark suit, outdoors"></div>
      </div>
      <div class="wordmark">PIMLU</div>
    </div>
    <div class="side-tab"></div>

    <div class="agent">
      <h1 class="agent-name">DANE MORROW</h1>
      <p class="agent-role">Licenced Real Estate Agent</p>
    </div>

    <div class="contact">
      <p class="address">PO Box 1187<br>Larkfield NSW 2790</p>
      <p class="contact-line">0400 318 552
        <svg viewBox="0 0 16 16" aria-hidden="true"><path d="M4 1.5l2.5 3-1.5 1.5c.8 1.8 2.2 3.2 4 4l1.5-1.5 3 2.5-1.5 2.5C7 13 3 9 1.5 3.5z" fill="var(--brand-red)"/></svg>
      </p>
      <p class="contact-line">dane@pimlu.com
        <svg viewBox="0 0 16 16" aria-hidden="true"><rect x="1.5" y="3.5" width="13" height="9" fill="none" stroke="var(--brand-red)" stroke-width="1.6"/><path d="M1.5 3.5l6.5 5 6.5-5" fill="none" stroke="var(--brand-red)" stroke-width="1.6"/></svg>
      </p>
      <p class="contact-line">www.pimlu.com
        <svg viewBox="0 0 16 16" aria-hidden="true"><g fill="none" stroke="var(--brand-red)" stroke-width="1.3"><circle cx="8" cy="8" r="6.5"/><ellipse cx="8" cy="8" rx="3" ry="6.5"/><path d="M1.5 8h13M2.5 4.8h11M2.5 11.2h11"/></g></svg>
      </p>
    </div>
  </section>

</main>
</body>
</html>
```